We are a local Communty Pharmacy wishing to promote and market a specialised Pharmaceutical Service

We would like a design that is professional and enticing ( according to the brief In attached files)
We wish to Market Compounding Pharmacy as a specialist side of our business.
We have the expertise a purpose built preparation laboratory.
The main purpose is an Internet presence that entices prospective patients to contact or visit our physical store.

Target Market(s)

Patients Medicos and Veterinary clients

Industry/Entity Type

Pharmacy

Coding

Coded - Design and coding required

Number of Pages Required

1 page

Requirements
Must have
• Clear friendly image
Nice to have
• soft enticing feel
Should not have
• No crass loud unprofessional elements

```html
<!DOCTYPE html>
<html lang="en">
<head>
<meta charset="utf-8">
<title>Mixwell Pharmacy – Compounding</title>
<link href="https://fonts.googleapis.com/css2?family=Open+Sans:wght@400;600;700&family=Lora:ital@1&display=swap" rel="stylesheet">
<style>
:root{
  --purple:#9a6fae;
  --purple-dark:#7e5792;
  --teal:#4fb7cf;
  --teal-dark:#3b9db5;
  --green:#94b63c;
  --green-dark:#7b9a2c;
  --violet:#a680b8;
  --violet-dark:#8c67a0;
  --orange:#f2a623;
  --orange-dark:#d98d12;
  --ink:#444;
  --muted:#8a8a8a;
  --line:#e4e4e4;
  --footer:#52b5cd;
  --footer-dark:#3e9fb8;
}
*{margin:0;padding:0;box-sizing:border-box}
html,body{width:788px;height:1200px;overflow:hidden;background:#fff}
body{font-family:"Open Sans",Arial,sans-serif;color:var(--ink);position:relative}
.topbar{height:18px;background:var(--purple);color:#fff;font-size:8px;display:flex;align-items:center;justify-content:space-between;padding:0 26px}
.topbar span{margin-right:14px}
.header{height:38px;display:flex;align-items:center;justify-content:space-between;padding:0 30px}
.logo{display:flex;align-items:center;gap:7px;font-size:19px;font-weight:600;color:var(--purple)}
.logo i{width:16px;height:16px;border-radius:50%;background:var(--orange);display:block}
.nav{display:flex;gap:30px;font-size:9px;color:#555}
.hero{position:absolute;top:56px;left:0;width:788px;height:352px;background:linear-gradient(90deg,#e9eef2 0%,#dfe6eb 45%,#f2f2f2 65%,#e7ebef 100%)}
.hero-photo{position:absolute;inset:0}
.hero-text{position:absolute;left:92px;top:38px}
.hero h1{font-size:31px;line-height:34px;color:var(--purple);font-weight:600}
.hero p{width:210px;font-size:11px;color:#fff;background:rgba(154,111,174,.55);padding:2px 4px;margin-top:4px}
.btn{display:inline-block;background:var(--teal);color:#fff;font-size:9px;padding:7px 14px;border-radius:2px}
.hero .btn{margin-top:22px}
.features{position:absolute;top:373px;left:79px;display:flex;gap:10px}
.feature{width:150px;height:106px;display:flex;flex-direction:column;box-shadow:0 2px 4px rgba(0,0,0,.15)}
.feature .icon{flex:1;display:flex;align-items:center;justify-content:center}
.feature .label{height:22px;font-size:9px;color:#fff;text-align:center;line-height:22px}
.f1 .icon{background:var(--teal)} .f1 .label{background:var(--teal-dark)}
.f2 .icon{background:var(--green)} .f2 .label{background:var(--green-dark)}
.f3 .icon{background:var(--violet)} .f3 .label{background:var(--violet-dark)}
.f4 .icon{background:var(--orange)} .f4 .label{background:var(--orange-dark)}
.tagline{position:absolute;top:515px;left:0;width:788px;text-align:center;font-family:"Lora",Georgia,serif;font-style:italic;font-size:12px;line-height:20px;color:#555}
.rule{position:absolute;left:79px;width:630px;height:1px;background:var(--line)}
.about{position:absolute;top:590px;left:79px;width:630px;display:flex;gap:26px}
.about-photo{width:190px;height:160px;background:radial-gradient(ellipse at 50% 65%,#7fd0d3 0%,#b9e3e5 45%,#fff 75%)}
.about h2{font-size:17px;font-weight:600;color:#444;margin-top:4px}
.about p{font-size:8px;line-height:13px;color:var(--muted);margin-top:10px}
.about .btn{margin-top:14px}
.clients{position:absolute;top:812px;left:0;width:788px;text-align:center;font-size:18px;font-weight:600;color:#444}
.testimonials{position:absolute;top:862px;left:79px;width:630px;display:flex;justify-content:space-between}
.testimonial{width:195px;display:flex;gap:10px}
.avatar{width:48px;height:48px;border-radius:50%;background:linear-gradient(#d9c2a8,#a9856a);flex:none}
.testimonial h3{font-size:10px;color:var(--orange);font-weight:600}
.testimonial small{display:block;font-size:7px;color:var(--muted)}
.testimonial p{font-size:7px;line-height:11px;color:var(--muted);margin-top:4px}
.footer{position:absolute;top:980px;left:0;width:788px;height:177px;background:var(--footer);color:#fff;padding:24px 79px 0;display:flex;gap:34px}
.footer h4{font-size:10px;font-weight:600;margin-bottom:8px}
.footer li{list-style:none;font-size:8px;line-height:14px}
.col{width:120px}
.map{width:150px;height:110px;margin-left:auto;background:linear-gradient(135deg,#eef0e8,#dfe5da)}
.copy{position:absolute;top:1157px;left:0;width:788px;height:43px;background:var(--footer-dark);color:#fff;font-size:8px;display:flex;align-items:center;padding:0 79px}
</style>
</head>
<body>
<div class="topbar">
  <div><span>(+61) 3 9000 4821</span><span>care@mixwellpharmacy.example</span></div>
  <div>Consult with your expert</div>
</div>
<header class="header">
  <div class="logo"><i></i>Mixwell Pharmacy</div>
  <nav class="nav"><span>Home</span><span>About us</span><span>Locations</span><span>Timings</span><span>Contact</span></nav>
</header>

<section class="hero">
  <div class="hero-photo" role="img" aria-label="Smiling pharmacist in a white coat in a bright pharmacy"></div>
  <div class="hero-text">
    <h1>Compounding<br>Pharmacy</h1>
    <p>The practice of making up medicines has been passed down from the 16th century</p>
    <a class="btn">Read more info</a>
  </div>
</section>

<div class="features">
  <div class="feature f1"><div class="icon"><svg width="40" height="40" viewBox="0 0 40 40" fill="#fff"><path d="M6 18h28c0 9-6 14-14 14S6 27 6 18z"/><rect x="14" y="32" width="12" height="3"/><rect x="22" y="4" width="4" height="16" transform="rotate(30 24 12)"/></svg></div><div class="label">We do Compounding</div></div>
  <div class="feature f2"><div class="icon"><svg width="40" height="40" viewBox="0 0 40 40" fill="#fff"><path d="M20 4a11 11 0 0 0-11 11c0 9 11 21 11 21s11-12 11-21A11 11 0 0 0 20 4zm0 15a4 4 0 1 1 0-8 4 4 0 0 1 0 8z"/></svg></div><div class="label">Where are you</div></div>
  <div class="feature f3"><div class="icon"><svg width="40" height="40" viewBox="0 0 40 40" fill="none" stroke="#fff" stroke-width="3"><circle cx="20" cy="20" r="15"/><path d="M20 10v10l7 5"/></svg></div><div class="label">When are we there</div></div>
  <div class="feature f4"><div class="icon"><svg width="40" height="40" viewBox="0 0 40 40" fill="#fff"><rect x="14" y="4" width="12" height="20" rx="6"/><path d="M9 19a11 11 0 0 0 22 0" fill="none" stroke="#fff" stroke-width="3"/><rect x="18.5" y="30" width="3" height="5"/><rect x="13" y="34" width="14" height="3"/></svg></div><div class="label">How can you contact</div></div>
</div>

<p class="tagline">To provide an awareness of where we are... that we are in the specialty business of compounding pharmacy...<br>And we want people to contact and visit our physical store</p>
<div class="rule" style="top:572px"></div>

<section class="about">
  <div class="about-photo" role="img" aria-label="Teal capsules spilling from a white pill bottle"></div>
  <div>
    <h2>About Compounding Pharmacy</h2>
    <p>Well ready for a lasting ease. The practice of making up medicines has been passed down from the 16th century and its necessity has only been heightened with the arrival of commercial drug manufacturing in our modern age.</p>
    <p>We find the positive aspect of knowing every part of a prepared medicine from the pharmacist directly, including the ability to counsel patients on their health and medication issues.</p>
    <a class="btn">Read more</a>
  </div>
</section>
<div class="rule" style="top:790px"></div>

<h2 class="clients">Happy Client's</h2>
<div class="testimonials">
  <div class="testimonial"><div class="avatar" role="img" aria-label="Client portrait"></div><div><h3>Marcus Hale</h3><small>Business man</small><p>Lovely staff and a simple blend made just for me, prepared quickly and clearly explained.</p></div></div>
  <div class="testimonial"><div class="avatar" role="img" aria-label="Client portrait"></div><div><h3>Marcus Hale</h3><small>Business man</small><p>Lovely staff and a simple blend made just for me, prepared quickly and clearly explained.</p></div></div>
  <div class="testimonial"><div class="avatar" role="img" aria-label="Client portrait"></div><div><h3>Marcus Hale</h3><small>Business man</small><p>Lovely staff and a simple blend made just for me, prepared quickly and clearly explained.</p></div></div>
</div>

<footer class="footer">
  <div class="col"><h4>Welcome</h4><ul><li>Home</li><li>About us</li><li>Locations</li><li>Timings</li><li>Contact</li></ul></div>
  <div class="col"><h4>Information</h4><ul><li>Terms &amp; Conditions</li><li>Privacy Policy</li><li>Disclaimer</li><li>Sitemap</li></ul></div>
  <div class="col" style="width:170px"><h4>Contact Info</h4><ul><li>12 Linden Parade, Elmsford</li><li>VIC 3190, Australia</li><li>(+61) 3 9000 4821</li><li>care@mixwellpharmacy.example</li><li>Mon-Fri 9am–6pm, Sat 9am–1pm</li></ul></div>
  <div class="map" role="img" aria-label="Street map showing the pharmacy location"></div>
</footer>
<div class="copy">© 2024 Mixwell Pharmacy. All rights reserved.</div>
</body>
</html>
```